Create a landing page for a new product market combination for an international software company

We are a software company being in the BtoB market for over 20 years. Our product is a software tool that allows for very flexible and versatile cost calculations for companies. We sell to all industries in over 40 countries with 500 clients. We have fairly recently seen a succesfull "competitor" (www.vorlinex.com) come up in the niche market of IT costing. This competitor has launched an independent platform with regards to managing IT costs (www.QRHguild.org). In this independent platform standards are set, events are organised and books are written. Since our software can handle all type of costing questions we can en already do play a role in IT costing. We have therefore become a sponsor of the QRH guild. Besides that we came accross the opportunity to buy the URL: www.qrhsoftware.com Which we did. We are now looking for a design on that landing page that communicates the fact that the visitor has landed with a company that have in depth knowledge on the QRH subject and provide an effective an affordable tooling for QRH. Currently the difference between the professionalism of our own website (www.pricelumen.com) and that of the competitor (www.vorlinex.com) and the independent council (www.qrhguild.org). is too big.

Target Market(s)

BtB with large IT spend

Number of Pages Required

1 page

Colors

Designer to choose colors to be used in the design.

Requirements
Must have
• A proffessional look and feel
Should not have
• Definetely not too much information and wording

```html
<!DOCTYPE html>
<html lang="en">
<head>
<meta charset="utf-8">
<title>PriceLumen – Technology Business Management</title>
<link href="https://fonts.googleapis.com/css2?family=Lora:wght@400;700&family=Montserrat:wght@400;600;700&family=Open+Sans:wght@400;600&display=swap" rel="stylesheet">
<style>
:root{
  --blue:#1d6aa6;--blue-dark:#175a8e;--navy:#0d3b8a;--ink:#111;--text:#333;--muted:#666;
  --topbar:#ececec;--hero:#242424;--white:#fff;--line:#d8d8d8;--red:#e0201b;--fb:#1f4f9c;
}
*{box-sizing:border-box;margin:0;padding:0}
html,body{width:1200px;height:3130px;overflow:hidden;background:var(--white)}
body{position:relative;font-family:'Open Sans',sans-serif;color:var(--text)}
.abs{position:absolute}
.topbar{left:0;top:0;width:1200px;height:38px;background:var(--topbar);font-size:14px;color:#333}
.topbar span{position:absolute;top:10px;display:flex;align-items:center;gap:8px}
.header{left:0;top:38px;width:1200px;height:129px;background:var(--blue)}
.brand{position:absolute;left:115px;top:38px;display:flex;align-items:center;gap:10px;color:var(--white);font-family:'Lora',serif;font-size:40px}
.brand i{display:block;width:18px;height:18px;background:var(--white)}
.nav{position:absolute;left:424px;top:58px;display:flex;gap:31px;color:var(--white);font-size:15px}
.social-side{left:1154px;top:119px;display:flex;flex-direction:column;gap:8px}
.social-side b{display:block;width:28px;height:28px;border-radius:4px;background:var(--fb)}
.social-side b.yt{border-radius:50%;background:var(--red)}
.hero{left:0;top:167px;width:1200px;height:584px;background:linear-gradient(135deg,#2c2c2c,#1b1b1b 60%,#262626)}
.hero-title{left:100px;top:345px;width:456px;text-align:center;font-family:'Lora',serif;font-size:46px;line-height:64px;color:var(--white)}
.btn{display:inline-block;background:var(--blue);color:var(--white);font-family:'Montserrat',sans-serif;font-weight:700;font-size:13px;border-radius:5px;text-align:center;line-height:34px;height:34px}
.hero-shot{left:559px;top:259px;width:535px;height:430px;border-radius:6px;background:linear-gradient(180deg,#d9d9d9 0,#bdbdbd 70%,#9a9a9a 100%)}
.dots{left:556px;top:709px;display:flex;gap:17px}
.dots i{display:block;width:10px;height:10px;border-radius:50%;background:var(--white)}
.dots i.on{background:var(--blue)}
.section-title{left:0;width:1200px;text-align:center;font-family:'Lora',serif;font-weight:700;font-size:52px;color:var(--ink)}
.svc{width:311px;height:297px;display:flex;align-items:center;justify-content:center;text-align:center;color:var(--white);font-family:'Lora',serif;font-weight:700;font-size:26px;line-height:42px;padding:0 30px}
.svc-focus{left:442px;top:918px;width:311px;height:349px;background:var(--blue);color:var(--white);text-align:center;padding:0 28px}
.svc-focus h3{font-family:'Lora',serif;font-weight:700;font-size:26px;line-height:34px;margin-top:112px}
.svc-focus p{font-size:14px;line-height:25px;margin-top:16px}
.grip-img{left:115px;top:1663px;width:476px;height:405px;background:linear-gradient(135deg,#4a4f5c,#8b8f98 50%,#c9bfae)}
.grip-title{left:614px;top:1733px;font-family:'Lora',serif;font-weight:700;font-size:52px;color:var(--ink)}
.grip-text{left:620px;top:1826px;width:468px;font-size:14px;line-height:25.5px;text-align:justify;color:#444}
.news{width:311px;height:388px;border:1px solid var(--line);background:var(--white);text-align:center}
.news .pic{height:194px;position:relative}
.news .date{position:absolute;left:14px;top:10px;width:36px;height:46px;background:var(--blue);color:var(--white);font-family:'Montserrat',sans-serif;font-weight:700;font-size:14px;line-height:15px;padding-top:8px}
.news .date small{display:block;font-size:10px}
.news h4{font-family:'Montserrat',sans-serif;font-weight:700;font-size:18px;color:var(--ink);margin-top:25px}
.news p{font-size:13px;line-height:24px;color:#555;padding:0 22px;margin-top:12px}
.news .btn{position:absolute;left:100px;top:363px;width:112px}
.newsletter{left:0;top:2709px;width:1200px;height:236px;background:linear-gradient(120deg,#0c3a86,#1a4fa4 50%,#0b3478)}
.newsletter h2{position:absolute;left:111px;top:48px;font-family:'Lora',serif;font-weight:700;font-size:50px;color:var(--white)}
.newsletter p{position:absolute;left:111px;top:130px;width:540px;font-size:13px;line-height:25px;color:var(--white)}
.field{position:absolute;left:733px;top:106px;width:348px;height:46px;border:2px solid var(--white);display:flex}
.field span{flex:1;padding-left:18px;line-height:42px;color:var(--white);font-style:italic;font-size:13px}
.field b{width:74px;border-left:2px solid var(--white);display:flex;align-items:center;justify-content:center}
.footer-nav{left:0;top:2979px;width:1200px;display:flex;justify-content:center;gap:40px;font-size:15px;color:#333;padding-left:16px}
.footer-social{left:0;top:3022px;width:1200px;display:flex;justify-content:center;gap:8px}
.footer-social i{display:block;width:34px;height:34px;border-radius:50%;background:var(--fb)}
.footer-social i.yt{background:var(--red)}
.copy{left:0;top:3073px;width:1200px;text-align:center;font-size:15px;color:#333}
</style>
</head>
<body>
<div class="abs topbar">
  <span style="left:310px"><svg width="14" height="14" viewBox="0 0 24 24"><path fill="#222" d="M6.6 10.8a15 15 0 006.6 6.6l2.2-2.2c.3-.3.7-.4 1-.2 1.1.4 2.3.6 3.6.6.6 0 1 .4 1 1V20c0 .6-.4 1-1 1A17 17 0 013 4c0-.6.4-1 1-1h3.5c.6 0 1 .4 1 1 0 1.3.2 2.5.6 3.6.1.3 0 .7-.2 1z"/></svg>1-800 555 0142</span>
  <span style="left:470px"><svg width="14" height="14" viewBox="0 0 24 24"><circle cx="12" cy="12" r="10" fill="#222"/><path d="M12 6v6l4 2" stroke="#fff" stroke-width="2" fill="none"/></svg>Monday - Friday 9:00 - 18:00</span>
  <span style="left:722px"><svg width="14" height="12" viewBox="0 0 24 18"><rect width="24" height="18" rx="2" fill="#222"/><path d="M1 2l11 8 11-8" stroke="#fff" stroke-width="2" fill="none"/></svg>info@pricelumen.com</span>
  <span style="left:925px"><svg width="14" height="14" viewBox="0 0 24 24"><circle cx="10" cy="10" r="7" stroke="#222" stroke-width="3" fill="none"/><path d="M15 15l7 7" stroke="#222" stroke-width="3"/></svg></span>
  <span style="left:983px">English <svg width="14" height="10"><rect width="14" height="10" fill="#3a4c9a"/><path d="M0 5h14M7 0v10" stroke="#d22" stroke-width="2"/></svg><svg width="10" height="8" style="margin-left:6px"><path d="M1 2l4 4 4-4" stroke="#222" stroke-width="2" fill="none"/></svg></span>
</div>

<header class="abs header">
  <div class="brand"><i></i>PriceLumen</div>
  <nav class="nav"><span>Home</span><span>Product</span><span>Markets</span><span>Company</span><span>Partners</span><span>Events</span><span>Support</span><span>Contact</span></nav>
</header>
<div class="abs social-side"><b></b><b class="yt"></b><b></b></div>

<section class="abs hero"></section>
<h1 class="abs hero-title" style="font-weight:400">Technology Business Management</h1>
<a class="abs btn" style="left:271px;top:503px;width:111px">Read more</a>
<div class="abs hero-shot" role="img" aria-label="Desktop monitor showing the cost dashboard with gauge charts"></div>
<div class="abs dots"><i></i><i class="on"></i><i></i><i></i></div>

<h2 class="abs section-title" style="top:800px">Our Services</h2>
<div class="abs svc" style="left:113px;top:970px;background:linear-gradient(135deg,#3c3f44,#6d7075)" role="img" aria-label="Man working at a desk">Position for Value</div>
<div class="abs svc-focus">
  <svg class="abs" style="left:128px;top:26px" width="56" height="64" viewBox="0 0 56 64" fill="none" stroke="#fff" stroke-width="2.5"><path d="M40 2a9 9 0 019 9c0 7-9 16-9 16s-9-9-9-16a9 9 0 019-9z"/><circle cx="40" cy="11" r="3"/><path d="M14 30a9 9 0 019 9c0 7-9 16-9 16s-9-9-9-16a9 9 0 019-9z"/><circle cx="14" cy="39" r="3"/><path d="M40 30v6h-10M14 58h26a6 6 0 000-12h-6" stroke-dasharray="4 3"/></svg>
  <h3>Continuously Improve</h3>
  <p>Execute a strategic roadmap for QRH maturity by integrating QRH into your day-to-day processes and thinking, so that QRH drives every value conversation with your peers</p>
</div>
<div class="abs svc" style="left:776px;top:970px;background:linear-gradient(135deg,#4a3a30,#7a5a45)" role="img" aria-label="Person working on a laptop">Create Transparency</div>
<div class="abs svc" style="left:113px;top:1292px;background:radial-gradient(circle at 50% 50%,#3d6b4a,#14213a 70%)" role="img" aria-label="Network globe graphic">Shape Business Demand</div>
<div class="abs svc" style="left:442px;top:1292px;background:linear-gradient(180deg,#4a5a6a,#6f7c5a)" role="img" aria-label="Coin dropped into a piggy bank">Deliver Value for Money</div>
<div class="abs svc" style="left:776px;top:1292px;background:linear-gradient(180deg,#5a6a70,#8a8060)" role="img" aria-label="Person celebrating with a laptop">Plan &amp; Govern</div>

<div class="abs grip-img" role="img" aria-label="Hands using a calculator and laptop over financial charts"></div>
<h2 class="abs grip-title">Get a grip on costs</h2>
<p class="abs grip-text">Every company wants to improve performance. Success starts with a greater knowledge of how your company works today in terms of costs and capacity. Make your company's cost and capacity flow transparent by using PriceLumen's bold graphic user interface and get a grip.</p>
<a class="abs btn" style="left:620px;top:1953px;width:110px">Read more</a>

<h2 class="abs section-title" style="top:2115px">Our News</h2>
<article class="abs news" style="left:113px;top:2229px">
  <div class="pic" role="img" aria-label="Team joining hands over a table" style="background:linear-gradient(135deg,#8a6a4a,#c9b79a)"><div class="date">13<small>JAN</small></div></div>
  <h4>Nor again is there anyone</h4>
  <p>Sed ut perspiciatis unde omnis iste natus error sit voluptatem accusantium doloremque laudantium, totam rem aperiam...</p>
  <a class="btn">Read more</a>
</article>
<article class="abs news" style="left:445px;top:2229px">
  <div class="pic" role="img" aria-label="Laptop and printed charts on a desk" style="background:linear-gradient(135deg,#b8925e,#e0d8cc)"><div class="date">20<small>JUN</small></div></div>
  <h4>Nor again is there anyone</h4>
  <p>Sed ut perspiciatis unde omnis iste natus error sit voluptatem accusantium doloremque laudantium, totam rem aperiam...</p>
  <a class="btn">Read more</a>
</article>
<article class="abs news" style="left:778px;top:2229px">
  <div class="pic" role="img" aria-label="Colleagues giving a high five" style="background:linear-gradient(135deg,#6a4a3a,#d8d0c8)"><div class="date">20<small>JUN</small></div></div>
  <h4>Nor again is there anyone</h4>
  <p>Sed ut perspiciatis unde omnis iste natus error sit voluptatem accusantium doloremque laudantium, totam rem aperiam...</p>
  <a class="btn">Read more</a>
</article>

<section class="abs newsletter">
  <h2>Newsletter</h2>
  <p>Lorem ipsum dolor sit amet, consectetur adipisicing elit, sed do eiusmod tempor incididunt ut labore et dolore magna</p>
  <div class="field"><span>Enter your email here</span><b><svg width="20" height="20" viewBox="0 0 24 24" fill="none" stroke="#fff" stroke-width="2"><path d="M22 2L2 10l8 4 4 8z M22 2L10 14"/></svg></b></div>
</section>

<nav class="abs footer-nav"><span>Home</span><span>Product</span><span>Markets</span><span>Company</span><span>Partners</span><span>Events</span><span>Support</span><span>Contact</span></nav>
<div class="abs footer-social"><i></i><i class="yt"></i><i></i></div>
<p class="abs copy">© 2019 | www.pricelumen.com</p>
</body>
</html>
```